QRV Advisors needs a web site

We need a web site for www.qrvadvisors-example.com. QRV is a mergers and acquisition consulting company that focuses our buyer and seller services on logistics companies. We help put companies together, and help with legal and financial due diligence. We want the web site to express our service and show the logistics components. We want personalized images versus pictures of trucks and airplanes.

Our new logo uses Burgandy and grey colors. Image attached. We are not in to bold, big letters...classy, artistic, low key preferred. Confidentiality, experience, professional are what we want to express on the site.

All we expect for the first part of this project is a home page, and one subpage.  We are budgeting other funds for the technical aspects of the web site

Reason: All that I'm seeing so far is trucks, forklifts and planes. We are a legal mergers and acquisitions firm that focus on logistics. I like some of the images to say logistics, but really want it say legal, financial, and putting companies together. Will pay extra for the sub page if someone can impress us with a home page.

Reason: Swamped with another project at the moment...will work on this over the weekend and provide designer feedback and select final design by Tuesday

```html
<!DOCTYPE html>
<html lang="en">
<head>
<meta charset="utf-8">
<title>QRV Advisors — Home</title>
<link href="https://fonts.googleapis.com/css2?family=Open+Sans:wght@400;600&display=swap" rel="stylesheet">
<style>
:root{
  --burgundy:#a6093a;
  --burgundy-dark:#8a0730;
  --ink:#3a3a3a;
  --muted:#666;
  --page:#f4f4f4;
  --band:#e6e6e6;
  --footer:#2b2b2b;
  --white:#fff;
}
*{box-sizing:border-box;margin:0;padding:0}
html,body{width:680px;height:1200px;overflow:hidden}
body{position:relative;background:var(--page);font-family:"Open Sans",Arial,sans-serif;color:var(--ink)}
.abs{position:absolute}
.top-rule{left:0;top:0;width:680px;height:2px;background:var(--burgundy)}
.page-top{left:0;top:2px;width:680px;height:110px;background:linear-gradient(#e9e9e9,#f1f1f1)}
/* header */
.brand{left:38px;top:37px;width:180px;height:76px;background:linear-gradient(#fafafa,#dcdcdc);clip-path:polygon(0 0,100% 0,82% 100%,0 100%);box-shadow:0 2px 3px rgba(0,0,0,.2)}
.brand-mark{left:46px;top:62px;font-size:26px;font-weight:400;letter-spacing:3px;color:var(--ink)}
.brand-sep{left:122px;top:62px;width:1px;height:26px;background:#888}
.brand-name{left:129px;top:62px;font-size:8.5px;line-height:9px;letter-spacing:.5px;color:var(--ink)}
.brand-name b{font-weight:400;color:var(--burgundy)}
.nav{left:217px;top:42px;width:432px;height:68px;background:linear-gradient(#c20c45,var(--burgundy-dark));display:flex}
.nav a{flex:1;display:flex;flex-direction:column;align-items:center;justify-content:flex-end;padding-bottom:14px;color:var(--white);font-size:8.5px;letter-spacing:.4px;text-decoration:none;gap:8px}
.nav a.active{flex:0 0 55px;background:var(--burgundy-dark)}
.nav svg{width:20px;height:18px}
/* hero */
.hero{left:0;top:112px;width:680px;height:241px;background:linear-gradient(90deg,#f3f3f3 0%,#ececec 45%,#e2e2e2 100%)}
.hero-photo{left:290px;top:112px;width:390px;height:241px;background:linear-gradient(100deg,#eaeaea 0%,#c9ccd0 35%,#d8d6d2 65%,#e4e4e2 100%)}
.hero-title{left:54px;top:153px;font-size:14px;letter-spacing:1px;font-weight:400;color:var(--ink)}
.hero-copy{left:55px;top:175px;width:250px;font-size:8px;line-height:14.7px;color:#444}
.btn{display:flex;align-items:center;justify-content:center;gap:8px;color:var(--white);font-size:8.5px;border-radius:2px}
.btn-red{left:54px;top:286px;width:89px;height:23px;background:var(--burgundy)}
.btn-dark{left:150px;top:286px;width:89px;height:23px;background:#2e2e2e}
/* clients */
.clients{left:0;top:353px;width:680px;height:85px;background:var(--band)}
.client{top:390px;font-size:12px;color:#777;display:flex;align-items:center;gap:6px}
.client i{display:inline-block;width:12px;height:12px;background:#888}
.client i.round{border-radius:50%}
.search{left:525px;top:371px;width:113px;height:18px;background:var(--white);border:1px solid #bbb;border-radius:3px;font-size:7.5px;color:#888;padding:3px 6px}
.search svg{position:absolute;right:5px;top:4px}
/* sections */
.section-title{font-size:12px;letter-spacing:1px;font-weight:400;color:var(--ink)}
.section-title b{font-weight:400;color:var(--burgundy)}
.rule{height:1px;background:#ddd}
.card{top:503px;width:102px;height:107px;background:linear-gradient(#fafafa,#e6e6e6);border-bottom:2px solid #bbb;box-shadow:0 1px 3px rgba(0,0,0,.12);display:flex;align-items:center;justify-content:center}
.svc-name{top:617px;width:140px;text-align:center;font-size:9px;color:var(--burgundy)}
.svc-copy{top:636px;width:140px;text-align:center;font-size:7.5px;line-height:10px;color:var(--muted)}
.pill{top:676px;width:70px;height:14px;background:var(--burgundy);color:var(--white);border-radius:8px;font-size:7px;display:flex;align-items:center;justify-content:center}
.arrow{top:538px;width:26px;height:36px;background:var(--burgundy);display:flex;align-items:center;justify-content:center}
/* news */
.news-photo{left:56px;top:794px;width:178px;height:117px;border:3px solid #ddd;background:linear-gradient(#c7cfd6 0%,#dcd6c8 40%,#7a8590 55%,#5a6573 100%)}
.btn-news{left:57px;top:922px;width:93px;height:18px;background:var(--burgundy);color:var(--white);font-size:7.5px;display:flex;align-items:center;justify-content:center;border-radius:2px}
.article{width:180px}
.article svg{position:absolute;left:0;top:0}
.article h3{margin-left:24px;font-size:8px;font-weight:400;letter-spacing:.4px;color:var(--burgundy)}
.article p{margin-left:26px;font-size:7.5px;line-height:12px;color:var(--muted);margin-top:1px}
.article a{display:block;margin-left:26px;font-size:7.5px;color:var(--burgundy);text-decoration:none;margin-top:1px}
/* footer */
.footer{left:0;top:994px;width:680px;height:180px;background:var(--footer);color:var(--white)}
.foot-col{top:1026px}
.foot-col h4{font-size:10px;font-weight:400;letter-spacing:.6px;margin-bottom:14px}
.foot-col li{list-style:none;font-size:7.5px;line-height:16.6px;padding-left:2px}
.field{background:var(--white);color:#888;font-size:7px;padding:3px 5px}
.send{left:525px;top:1102px;width:92px;height:17px;background:var(--burgundy);color:var(--white);font-size:7.5px;display:flex;align-items:center;justify-content:center}
.base{left:0;top:1174px;width:680px;height:26px;background:var(--burgundy);color:var(--white);font-size:7.5px;padding:8px 0 0 54px}
.social{top:1180px;width:14px;height:14px;border-radius:50%;background:var(--white)}
</style>
</head>
<body>
<div class="abs top-rule"></div>
<div class="abs page-top"></div>

<header>
  <div class="abs brand"></div>
  <div class="abs brand-mark">QRV</div>
  <div class="abs brand-sep"></div>
  <div class="abs brand-name">QUALITY<br>ROUTE<br><b>VENTURES</b></div>
  <nav class="abs nav">
    <a class="active" href="#"><svg viewBox="0 0 20 18"><path d="M10 1 1 9h3v8h4v-5h4v5h4V9h3z" fill="#fff"/></svg>HOME</a>
    <a href="#"><svg viewBox="0 0 20 18"><circle cx="10" cy="9" r="8" fill="#fff"/><rect x="9" y="7.5" width="2" height="6" fill="#a6093a"/><circle cx="10" cy="5" r="1.2" fill="#a6093a"/></svg>ABOUT US</a>
    <a href="#"><svg viewBox="0 0 20 18"><path d="M4 5h4a2 2 0 1 1 4 0h4v4a2 2 0 1 1 0 4v4H4z" fill="#fff"/></svg>OUR SERVICES ▾</a>
    <a href="#"><svg viewBox="0 0 20 18"><rect x="2" y="5" width="16" height="11" rx="1.5" fill="#fff"/><rect x="7" y="2" width="6" height="4" rx="1" fill="none" stroke="#fff" stroke-width="1.5"/></svg>OUR CLIENTS</a>
    <a href="#"><svg viewBox="0 0 20 18"><rect x="2" y="4" width="16" height="11" fill="#fff"/><path d="M2 4l8 6 8-6" fill="none" stroke="#a6093a" stroke-width="1.2"/></svg>CONTACT US</a>
  </nav>
</header>

<section>
  <div class="abs hero"></div>
  <div class="abs hero-photo" role="img" aria-label="Two business advisors shaking hands in a bright office"></div>
  <h1 class="abs hero-title">QRV ADVISORS</h1>
  <p class="abs hero-copy">QRV assists business owners within the logistics industry to implement growth and exit strategies. We offer business planning and merger and acquisition(M&amp;A) advisory services. QRV services are offered by industry executives with extensive M&amp;A experience.&nbsp; Your company will benefit from a unique and outside perspective from consultants that understand your business.</p>
  <div class="abs btn btn-red">Read more <svg width="7" height="7" viewBox="0 0 7 7"><path d="M0 0l7 3.5L0 7z" fill="#fff"/></svg></div>
  <div class="abs btn btn-dark">Contact us <svg width="9" height="7" viewBox="0 0 9 7"><rect width="9" height="7" fill="#fff"/></svg></div>
</section>

<section>
  <div class="abs clients"></div>
  <div class="abs client" style="left:57px"><i></i>HALBROOK</div>
  <div class="abs client" style="left:186px">NORTHGATE TRUST</div>
  <div class="abs client" style="left:310px"><i class="round" style="width:36px;height:36px;margin-top:-12px"></i></div>
  <div class="abs client" style="left:396px"><i class="round"></i>Corvane</div>
  <div class="abs client" style="left:534px;top:396px">MARROW LEEDS</div>
  <div class="abs search">Keyword Search...<svg width="9" height="9" viewBox="0 0 9 9"><circle cx="3.5" cy="3.5" r="2.6" fill="none" stroke="#777" stroke-width="1.2"/><path d="M5.5 5.5 8.5 8.5" stroke="#777" stroke-width="1.4"/></svg></div>
</section>

<section>
  <h2 class="abs section-title" style="left:55px;top:456px">OUR <b>SERVICES</b></h2>
  <div class="abs rule" style="left:54px;top:478px;width:586px"></div>

  <div class="abs arrow" style="left:47px;border-radius:0 18px 18px 0;clip-path:inset(0 0 0 0);border-radius:18px 0 0 18px"><svg width="8" height="10"><path d="M8 0v10L0 5z" fill="#fff"/></svg></div>
  <div class="abs arrow" style="left:614px;border-radius:0 18px 18px 0"><svg width="8" height="10"><path d="M0 0v10l8-5z" fill="#fff"/></svg></div>

  <div class="abs card" style="left:63px"><svg width="64" height="66" viewBox="0 0 64 66"><g fill="#555"><rect x="2" y="44" width="6" height="20"/><rect x="12" y="38" width="6" height="26"/><rect x="22" y="32" width="6" height="32"/><rect x="32" y="26" width="6" height="38"/><rect x="42" y="20" width="6" height="44"/><rect x="52" y="14" width="6" height="50"/></g><path d="M2 40Q30 34 46 10" fill="none" stroke="#a6093a" stroke-width="6"/><path d="M38 8 58 0 54 20z" fill="#a6093a"/></svg></div>
  <div class="abs card" style="left:215px"><svg width="56" height="50" viewBox="0 0 56 50"><rect x="6" y="4" width="44" height="30" fill="none" stroke="#555" stroke-width="3"/><path d="M28 34v4M20 48l8-10 8 10" stroke="#555" stroke-width="3" fill="none"/><circle cx="28" cy="17" r="5" fill="#a6093a"/><g stroke="#a6093a" stroke-width="1.5"><path d="M28 8v-2M20 17h-2M36 17h2M22 11l-1.5-1.5M34 11l1.5-1.5"/></g></svg></div>
  <div class="abs card" style="left:362px"><svg width="44" height="54" viewBox="0 0 44 54"><path d="M4 22Q8 8 28 10V2l14 12-14 12v-8Q14 16 4 22z" fill="#a6093a"/><path d="M40 32Q36 46 16 44v8L2 40l14-12v8q14 2 24-4z" fill="#555"/></svg></div>
  <div class="abs card" style="left:512px"><svg width="56" height="46" viewBox="0 0 56 46"><rect x="20" y="2" width="16" height="11" fill="#a6093a"/><path d="M28 13v8M8 21h40M8 21v6M28 21v6M48 21v6" stroke="#555" stroke-width="2.5" fill="none"/><rect x="1" y="27" width="14" height="11" fill="#555"/><rect x="21" y="27" width="14" height="11" fill="#555"/><rect x="41" y="27" width="14" height="11" fill="#555"/></svg></div>

  <div class="abs svc-name" style="left:44px">Growth &amp; Exit Strategies</div>
  <div class="abs svc-name" style="left:194px">Business Planning</div>
  <div class="abs svc-name" style="left:344px">Merger &amp; Acquisition</div>
  <div class="abs svc-name" style="left:495px">Management System</div>
  <p class="abs svc-copy" style="left:44px">Lorem dipsum dolora sitame adipscing elit. Morabi nisll digula astren esequat art.</p>
  <p class="abs svc-copy" style="left:194px">Lorem dipsum dolora sitame adipscing elit. Morabi nisll digula astren esequat art.</p>
  <p class="abs svc-copy" style="left:344px">Lorem dipsum dolora sitame adipscing elit. Morabi nisll digula astren esequat art.</p>
  <p class="abs svc-copy" style="left:495px">Lorem dipsum dolora sitame adipscing elit. Morabi nisll digula astren esequat art.</p>
  <div class="abs pill" style="left:77px">more details +</div>
  <div class="abs pill" style="left:228px">more details +</div>
  <div class="abs pill" style="left:378px">more details +</div>
  <div class="abs pill" style="left:529px">more details +</div>
</section>

<section>
  <h2 class="abs section-title" style="left:55px;top:753px">LATEST <b>NEWS</b></h2>
  <div class="abs rule" style="left:54px;top:775px;width:595px"></div>
  <div class="abs news-photo" role="img" aria-label="Container port with stacked shipping containers and cranes under a cloudy sky"></div>
  <div class="abs btn-news">VIEW ALL ARTICLES</div>
  <div class="abs" style="left:450px;top:776px;width:1px;height:165px;background:#ddd"></div>
  <div class="abs rule" style="left:245px;top:858px;width:404px"></div>
  <div class="abs rule" style="left:54px;top:954px;width:595px"></div>

  <article class="abs article" style="left:250px;top:793px"><svg width="16" height="13" viewBox="0 0 16 13"><rect x=".5" y=".5" width="15" height="12" fill="none" stroke="#666"/><rect x="3" y="3" width="4" height="4" fill="#666"/><path d="M9 4h5M9 6h5M3 9h11" stroke="#666"/></svg><h3>TITLE OF THE ARTICLE GOES HERE</h3><p>Lorem ipsum dolor sit amet, con-sectetur adipiscing elit. Phasellus tincidunt tellus leo, sodales vestibu-</p><a href="#">Read more ⟶</a></article>
  <article class="abs article" style="left:465px;top:793px"><svg width="16" height="13" viewBox="0 0 16 13"><rect x=".5" y=".5" width="15" height="12" fill="none" stroke="#666"/><rect x="3" y="3" width="4" height="4" fill="#666"/><path d="M9 4h5M9 6h5M3 9h11" stroke="#666"/></svg><h3>TITLE OF THE ARTICLE GOES HERE</h3><p>Lorem ipsum dolor sit amet, con-sectetur adipiscing elit. Phasellus tincidunt tellus leo, sodales vestibu-</p><a href="#">Read more ⟶</a></article>
  <article class="abs article" style="left:250px;top:871px"><svg width="16" height="13" viewBox="0 0 16 13"><rect x=".5" y=".5" width="15" height="12" fill="none" stroke="#666"/><rect x="3" y="3" width="4" height="4" fill="#666"/><path d="M9 4h5M9 6h5M3 9h11" stroke="#666"/></svg><h3>TITLE OF THE ARTICLE GOES HERE</h3><p>Lorem ipsum dolor sit amet, con-sectetur adipiscing elit. Phasellus tincidunt tellus leo, sodales vestibu-</p><a href="#">Read more ⟶</a></article>
  <article class="abs article" style="left:465px;top:871px"><svg width="16" height="13" viewBox="0 0 16 13"><rect x=".5" y=".5" width="15" height="12" fill="none" stroke="#666"/><rect x="3" y="3" width="4" height="4" fill="#666"/><path d="M9 4h5M9 6h5M3 9h11" stroke="#666"/></svg><h3>TITLE OF THE ARTICLE GOES HERE</h3><p>Lorem ipsum dolor sit amet, con-sectetur adipiscing elit. Phasellus tincidunt tellus leo, sodales vestibu-</p><a href="#">Read more ⟶</a></article>
</section>

<footer>
  <div class="abs footer"></div>
  <div class="abs foot-col" style="left:53px;color:#fff"><h4>ABOUT US</h4><ul><li>Who we are</li><li>Client List</li><li>Contact Info</li></ul></div>
  <div class="abs foot-col" style="left:154px;color:#fff"><h4>SERVICES OFFERED</h4><ul><li>Growth &amp; Exit Strategies</li><li>Business Planning</li><li>Merger &amp; Aquisition</li><li>Management System</li></ul></div>
  <div class="abs foot-col" style="left:294px;color:#fff"><h4>ADDITIONAL INFO</h4><ul><li>Sitemap</li><li>FAQ</li><li>Privacy Policy</li><li>Terms &amp; Agreement</li></ul></div>
  <div class="abs foot-col" style="left:428px;color:#fff"><h4>QUICK MESSAGE</h4></div>
  <div class="abs field" style="left:428px;top:1055px;width:91px;height:17px">Firstname</div>
  <div class="abs field" style="left:428px;top:1078px;width:91px;height:17px">Email Address</div>
  <div class="abs field" style="left:428px;top:1102px;width:91px;height:17px">Contact #</div>
  <div class="abs field" style="left:525px;top:1055px;width:92px;height:40px">Message</div>
  <div class="abs send">Send Message</div>
  <div class="abs base">Quality Route Ventures All Rights Reserved ® 2014</div>
  <div class="abs social" style="left:561px"></div>
  <div class="abs social" style="left:580px"></div>
  <div class="abs social" style="left:600px"></div>
</footer>
</body>
</html>
```